Automotive component supplier needs a business card design

We need a business card design for our company called Velran Global Components Ltd based in the UK. We are a supplier of interior and exterior components to premium car manufacturers such as Corvel Ashby, Hadley Fenn, Marquist and Tavarelli. We would like to see a modern business card design that uses the colour blue.

Target Market(s)

Premium automotive car manufacturers.

Industry/Entity Type

Automotive

Contact Information for Business Card

Company Name : Velran Global Components Limited
Address: 17 Marlow Yard, Upper Heath, Warwick, CV31 8QL, United Kingdom
Web Address : www.velrancomponents-example.co.uk

Font styles to use
Other font styles liked:
• Helvetica

Colors
3176b5
0255a3
85acd3
cfdeed
cee9f5
85cae6
34a6d7
0692cd
9bcb3c

Requirements
Must have
• Clear company logo and a mixture of blue colours.
Nice to have
• A high quality modern image.
Should not have
• Multiple colours.

```html
<!DOCTYPE html>
<html lang="en">
<head>
<meta charset="utf-8">
<title>Velran Global Components – Business Card</title>
<link rel="stylesheet" href="https://fonts.googleapis.com/css2?family=Arimo:wght@400;700&display=swap">
<style>
  :root {
    --blue-brand: #0692cd;
    --blue-deep: #0255a3;
    --blue-mid: #34a6d7;
    --green-accent: #9bcb3c;
    --ink-grey: #5a5d61;
    --card-white: #ffffff;
    --backdrop: #e9edf1;
  }
  * { margin: 0; padding: 0; box-sizing: border-box; }
  html, body {
    width: 1200px; height: 950px; overflow: hidden;
    background: var(--backdrop);
    font-family: "Arimo", Helvetica, Arial, sans-serif;
  }
  .stage {
    position: relative; width: 1200px; height: 950px;
    display: flex; justify-content: center; align-items: center; gap: 60px;
  }
  .card {
    position: relative; width: 400px; height: 700px;
    box-shadow: 0 6px 18px rgba(0,0,0,0.15);
  }
  /* Front */
  .card--front { background: var(--card-white); color: var(--ink-grey); }
  .front__brand {
    position: absolute; top: 70px; left: 0; right: 0; text-align: center;
    color: var(--blue-brand); font-weight: 700; font-size: 30px;
    line-height: 1.1; letter-spacing: 0.5px;
  }
  .front__person { position: absolute; top: 300px; left: 42px; right: 30px; }
  .person__name {
    color: var(--blue-brand); font-weight: 700; font-size: 22px; letter-spacing: 0.5px;
  }
  .person__role { color: var(--green-accent); font-size: 17px; margin-top: 4px; }
  .person__address { margin-top: 10px; font-size: 16px; line-height: 1.35; }
  .contact-list { list-style: none; margin-top: 14px; font-size: 16px; line-height: 1.45; }
  .contact-list li { display: flex; align-items: center; gap: 10px; }
  .contact-list svg { width: 16px; height: 16px; flex: none; fill: var(--blue-brand); }
  /* Back */
  .card--back { background: var(--blue-brand); color: var(--card-white); }
  .back__brand {
    position: absolute; top: 250px; left: 0; right: 0; text-align: center;
    font-weight: 700; font-size: 40px; line-height: 1.1; letter-spacing: 0.5px;
  }
  .back__web {
    position: absolute; bottom: 70px; left: 0; right: 0; text-align: center;
    font-size: 15px; letter-spacing: 2.5px;
  }
</style>
</head>
<body>
<main class="stage">
  <section class="card card--front" aria-label="Business card front">
    <div class="front__brand">Velran Global<br>Components</div>
    <div class="front__person">
      <p class="person__name">DANIEL HARROW</p>
      <p class="person__role">CEO / Founder</p>
      <p class="person__address">17 Marlow Yard, Upper Heath<br>Warwick, CV31 8QL<br>United Kingdom</p>
      <ul class="contact-list">
        <li>
          <svg viewBox="0 0 16 16" aria-hidden="true"><path d="M3.5 1.5l2.5 2.7-1.4 1.9c.9 2 2.4 3.5 4.4 4.4l1.9-1.4 2.7 2.5-1.5 2.4C6.7 13.7 2.3 9.3 1.1 3z"/></svg>
          <span>614 902 3817</span>
        </li>
        <li>
          <svg viewBox="0 0 16 16" aria-hidden="true"><path d="M4.5 1h7a1 1 0 0 1 1 1v12a1 1 0 0 1-1 1h-7a1 1 0 0 1-1-1V2a1 1 0 0 1 1-1zm.5 2v9h6V3zm3 9.6a.8.8 0 1 0 0 1.6.8.8 0 0 0 0-1.6z"/></svg>
          <span>742 315 8806</span>
        </li>
        <li>
          <svg viewBox="0 0 16 16" aria-hidden="true"><path d="M1 3.5h14v9H1zm1.4 1L8 8.6l5.6-4.1z"/></svg>
          <span>daniel@velrancomponents-example.co.uk</span>
        </li>
        <li>
          <svg viewBox="0 0 16 16" aria-hidden="true"><circle cx="8" cy="8" r="7"/></svg>
          <span>www.velrancomponents-example.co.uk</span>
        </li>
      </ul>
    </div>
  </section>

  <section class="card card--back" aria-label="Business card back">
    <div class="back__brand">Velran Global<br>Components</div>
    <p class="back__web">www.velrancomponents-example.co.uk</p>
  </section>
</main>
</body>
</html>
```